DRUM needs a contemporary simple brochure

We help companies understand their customers, and we would like to send a minimalistic card/brochure to potential clients to introduce our company. The card will be A6 in size (ie A5 folded once) and so will have a front, an inside front, and inside back, and a back page. It can either be portrait or landscape.
It should convey contemporary/modern, bold, fun, uncomplicated/simplicity, be clean/uncluttered, and use friendly and easy to read fonts.
Attached is the information the brochure/card should contain, together with colour palatte and another document which shows our logo, existing stationary etc to give you a feel of the brand. The background of the card could be black, yellow or white (or a combination). thanks, mark
Updates
Hi everyone. Just to let you know that the card will be A6 size, will have a matt laminate finish and can include spot uv. thanks, mark
Reason: Hi, I am looking for some better quality designs so i have extended the deadline and significantly increased the budget. thanks, mark
Target Market(s)
Marketing professionals in large corporates
Industry/Entity Type
It Company
Requirements
Must have
- use our company colours (attached)

```html
<!DOCTYPE html>
<html lang="en">
<head>
<meta charset="utf-8">
<title>DRUM – Brochure Inside Spread</title>
<link rel="stylesheet" href="https://fonts.googleapis.com/css2?family=Fredoka:wght@600&display=swap">
<style>
:root{
  --backdrop:#e9e4dc;
  --panel:#3d3c3e;
  --accent:#f5c400;
  --icon-mark:#3d3c3e;
  --photo-top:#8a8580;
  --photo-bottom:#4a4744;
  --frame:#ffffff;
}
*{margin:0;padding:0;box-sizing:border-box}
html,body{width:1200px;height:1141px;overflow:hidden}
body{background:var(--backdrop);font-family:"Fredoka",sans-serif;font-weight:600;color:var(--accent);position:relative}
.panel{position:absolute;top:19px;height:1055px;background:var(--panel);overflow:hidden}
.panel--left{left:17px;width:573px}
.panel--right{left:604px;width:578px}
.section-title{position:absolute;left:20px;top:40px;font-size:23px;font-weight:600;line-height:1;letter-spacing:.3px}
.services{list-style:none}
.service{position:absolute;display:flex;align-items:flex-start;gap:10px;font-size:18px;line-height:24px;white-space:nowrap;letter-spacing:.2px}
.service svg{flex:none;margin-top:2px}
.copy{position:absolute;font-size:20px;line-height:28px;white-space:nowrap;letter-spacing:.3px}
.intro{left:24px;top:401px}
.photo{position:absolute;left:19px;top:618px;width:295px;height:272px;border:3px solid var(--frame);background:linear-gradient(180deg,var(--photo-top),var(--photo-bottom))}
.aside-copy{left:332px;top:615px;font-size:19.5px;line-height:27.8px}
.closing-copy{left:26px;top:904px;font-size:19.5px}
.brand-intro{left:20px;top:73px}
.brand-name{font-weight:600}
.body-copy{left:16px}
.indent{display:inline-block;width:106px}
.tagline{position:absolute;left:15px;top:886px;font-size:28px;font-weight:600;line-height:1;white-space:nowrap;letter-spacing:.3px}
.web{position:absolute;left:20px;top:933px;font-size:19px;line-height:1;white-space:nowrap;letter-spacing:.3px}
</style>
</head>
<body>
<section class="panel panel--left">
  <h2 class="section-title">Customer &amp; Shopper Market Research</h2>
  <ul class="services">
    <li class="service" style="left:23px;top:113px"><svg width="20" height="20" viewBox="0 0 20 20"><circle cx="10" cy="10" r="10" fill="var(--accent)"/><path d="M7.5 5.5 15 10l-7.5 4.5z" fill="var(--icon-mark)"/></svg><span>New Product<br>Development</span></li>
    <li class="service" style="left:301px;top:113px"><svg width="20" height="20" viewBox="0 0 20 20"><circle cx="10" cy="10" r="10" fill="var(--accent)"/><path d="M7.5 5.5 15 10l-7.5 4.5z" fill="var(--icon-mark)"/></svg>Online Communities</li>
    <li class="service" style="left:23px;top:179px"><svg width="20" height="20" viewBox="0 0 20 20"><circle cx="10" cy="10" r="10" fill="var(--accent)"/><path d="M7.5 5.5 15 10l-7.5 4.5z" fill="var(--icon-mark)"/></svg>Product Testing</li>
    <li class="service" style="left:301px;top:179px"><svg width="20" height="20" viewBox="0 0 20 20"><circle cx="10" cy="10" r="10" fill="var(--accent)"/><path d="M7.5 5.5 15 10l-7.5 4.5z" fill="var(--icon-mark)"/></svg>Customer Experience</li>
    <li class="service" style="left:23px;top:243px"><svg width="20" height="20" viewBox="0 0 20 20"><circle cx="10" cy="10" r="10" fill="var(--accent)"/><path d="M7.5 5.5 15 10l-7.5 4.5z" fill="var(--icon-mark)"/></svg>Retail</li>
    <li class="service" style="left:301px;top:243px"><svg width="20" height="20" viewBox="0 0 20 20"><circle cx="10" cy="10" r="10" fill="var(--accent)"/><path d="M7.5 5.5 15 10l-7.5 4.5z" fill="var(--icon-mark)"/></svg>Visualisation</li>
    <li class="service" style="left:23px;top:309px"><svg width="20" height="20" viewBox="0 0 20 20"><circle cx="10" cy="10" r="10" fill="var(--accent)"/><path d="M7.5 5.5 15 10l-7.5 4.5z" fill="var(--icon-mark)"/></svg><span>Customer<br>Segmentation</span></li>
    <li class="service" style="left:301px;top:309px"><svg width="20" height="20" viewBox="0 0 20 20"><circle cx="10" cy="10" r="10" fill="var(--accent)"/><path d="M7.5 5.5 15 10l-7.5 4.5z" fill="var(--icon-mark)"/></svg>Bespoke Research</li>
  </ul>
  <p class="copy intro">Drum has a team of Experts to undertake<br>various studies related to your Business,<br>specially the Customer feedback, Customer<br>experience, Customer segmentation etc., in<br>order to facilitate the management to take<br>further steps to boost up your Business and<br>thus increase the profitability.</p>
  <div class="photo" role="img" aria-label="Portrait photograph of a team member"></div>
  <p class="copy aside-copy">Lorem ipsum dolor<br>sit amet, consecte<br>dipisicing elit, sed<br>do eiusmod temp<br>incidid ut labore<br>dolore magna aliq<br>Utenim ad ris nisi<br>ut aliquip ex eaco<br>mmodo conseq.<br>Lorem ipsum dolo.</p>
  <p class="copy closing-copy">Lorem ipsum dolor sit amet, consecte dipisic<br>ing elit, sed do eiusmod tempor incididuut la<br>bore et dolore magna aliqua.Ut enim ad min<br>im veniam, quis nostrud exercitation ullam<br>laboris nisi.</p>
</section>

<section class="panel panel--right">
  <p class="copy brand-intro"><span class="brand-name">DRUM</span> is a progressive, technology friendly<br>market research agency, specialising in<br>customer and shopper research. We help<br>companies understand the ever-changing<br>relationships people have with media,<br>services, products and brands by combining<br>innovative methods, creative thinking,<br>research expertise and a deep understanding<br>of shopper and consumer decision-making.</p>
  <p class="copy body-copy" style="top:334px"><span class="indent"></span>We offer cost effective research,<br>designed and managed by experienced<br>practitioners, using award winning online,<br>mobile, community and video based research<br>applications.</p>
  <p class="copy body-copy" style="top:494px;left:19px"><span class="indent"></span>Lorem ipsum dolor sit amet, consecte<br>dipisicing elit, sed do eiusmod tempor incidid<br>ut labore et dolore magna aliqua.Utenim ad<br>ris nisi ut aliquip ex ea commodo conseq.<br>Lorem ipsum dolor sit amet,consectetur adipis<br>sed do eiusmod tempor incididunt ut labore et.</p>
  <p class="copy body-copy" style="top:706px;left:19px"><span class="indent"></span>Lorem ipsum dolor sit amet, consecte<br>dipisicing elit, sed do eiusmod tempor incididu<br>ut labore et dolore magna aliqua.Ut enim ad<br>minim veniam, quis nostrud exercitation ullam<br>laboris nisi.</p>
  <h2 class="tagline">Understand your customers better</h2>
  <p class="web">find out more at www.drummr.com.au</p>
</section>
</body>
</html>
```